BOLD & MINIMALIST DESIGN NEEDED

We want a very bold but minimalistic business card design that is impactful and utilizes both sides of the business card. Our current logo is included for your use.

We want bold fonts and good use of negative space. We don't want the logo to overpower the design.

Target Market(s)

Professionals who are building new commercial buildings.

Industry/Entity Type

Construction

Contact Information for Business Card

Name, Title, email, office phone, cell phone, website

Font styles to use
Serif
Sans Serif

Requirements
Must have
• Bold design!

```html
<!DOCTYPE html>
<html lang="en">
<head>
<meta charset="utf-8">
<title>Northcrest Design + Build — Business Card</title>
<link rel="stylesheet" href="https://fonts.googleapis.com/css2?family=Poppins:wght@400;500;700;800&display=swap">
<style>
  :root {
    --ink: #0d0d0d;
    --paper: #ffffff;
    --green: #7cc82e;
    --stage: #e9e9e9;
    --muted: #f2f2f2;
  }
  * { box-sizing: border-box; margin: 0; padding: 0; }
  html, body {
    width: 1200px; height: 900px; overflow: hidden;
    background: var(--stage);
    font-family: "Poppins", sans-serif;
  }
  .canvas { position: relative; width: 1200px; height: 900px; }
  .card {
    position: absolute; left: 250px; width: 700px; height: 400px;
    border-radius: 26px; overflow: hidden;
    box-shadow: 0 10px 30px rgba(0,0,0,.18);
  }
  .card--front { top: 40px; background: var(--ink); }
  .card--back { top: 470px; background: var(--paper); }

  .wordmark {
    position: absolute; left: 0; right: 0;
    display: flex; align-items: center; justify-content: center; gap: 18px;
    font-weight: 800; text-transform: uppercase; line-height: 1;
  }
  .wordmark__mark { width: 22px; height: 22px; background: var(--green); flex: none; }
  .wordmark__text { display: flex; flex-direction: column; align-items: center; }
  .wordmark__name { font-size: 54px; letter-spacing: 1px; }
  .wordmark__tag { font-size: 17px; letter-spacing: 9px; margin-top: 10px; }
  .card--front .wordmark { top: 150px; color: var(--paper); }
  .card--back .wordmark { top: 50px; color: var(--ink); }
  .card--back .wordmark__name { font-size: 44px; }
  .card--back .wordmark__tag { font-size: 14px; letter-spacing: 7px; margin-top: 8px; }

  .wave { position: absolute; inset: 0; width: 700px; height: 400px; }

  .person {
    position: absolute; left: 60px; top: 250px; width: 250px;
    text-align: right; color: var(--paper);
  }
  .person__name { color: var(--green); font-weight: 700; font-size: 25px; line-height: 1.15; }
  .person__title { font-size: 15px; margin-bottom: 6px; }
  .person__address { font-size: 14.5px; line-height: 1.4; }

  .divider {
    position: absolute; left: 330px; top: 258px; width: 2px; height: 100px;
    background: var(--green);
  }

  .contacts {
    position: absolute; left: 352px; top: 272px;
    list-style: none; color: var(--paper); font-size: 14.5px;
  }
  .contacts li { display: flex; align-items: center; gap: 10px; line-height: 1.55; }
  .contacts svg { width: 13px; height: 13px; fill: var(--green); flex: none; }
</style>
</head>
<body>
<main class="canvas">

  <section class="card card--front" aria-label="Card front">
    <div class="wordmark">
      <span class="wordmark__mark"></span>
      <div class="wordmark__text">
        <span class="wordmark__name">Northcrest</span>
        <span class="wordmark__tag">Design + Build</span>
      </div>
    </div>
  </section>

  <section class="card card--back" aria-label="Card back">
    <div class="wordmark">
      <span class="wordmark__mark"></span>
      <div class="wordmark__text">
        <span class="wordmark__name">Northcrest</span>
        <span class="wordmark__tag">Design + Build</span>
      </div>
    </div>

    <svg class="wave" viewBox="0 0 700 400" aria-hidden="true">
      <path d="M0,163 Q350,100 700,306 L700,330 Q350,120 0,176 Z" fill="var(--green)"/>
      <path d="M0,176 Q350,120 700,330 L700,400 L0,400 Z" fill="var(--ink)"/>
    </svg>

    <div class="person">
      <p class="person__name">Daniel Reyes</p>
      <p class="person__title">Head contractor</p>
      <p class="person__address">1420 Cedar Hollow Rd.<br>Mapleton, GA 30599</p>
    </div>

    <div class="divider"></div>

    <ul class="contacts">
      <li>
        <svg viewBox="0 0 24 24"><path d="M6.6 10.8a15 15 0 0 0 6.6 6.6l2.2-2.2c.3-.3.7-.4 1-.2 1.1.4 2.3.6 3.6.6.6 0 1 .4 1 1V20c0 .6-.4 1-1 1A17 17 0 0 1 3 4c0-.6.4-1 1-1h3.5c.6 0 1 .4 1 1 0 1.3.2 2.5.6 3.6.1.3 0 .7-.2 1z"/></svg>
        555.014.2200
      </li>
      <li>
        <svg viewBox="0 0 24 24"><path d="M7 1h10a2 2 0 0 1 2 2v18a2 2 0 0 1-2 2H7a2 2 0 0 1-2-2V3a2 2 0 0 1 2-2zm0 3v14h10V4zm5 15.5a1 1 0 1 0 0 2 1 1 0 0 0 0-2z"/></svg>
        555-014-2201
      </li>
      <li>
        <svg viewBox="0 0 24 24"><path d="M2 5h20v2l-10 6L2 7zm0 4.3 10 6 10-6V19H2z"/></svg>
        info@ncdb-build.com
      </li>
      <li>
        <svg viewBox="0 0 24 24"><path d="M12 2a10 10 0 1 0 0 20 10 10 0 0 0 0-20zm0 2c.9 1.2 1.6 2.6 2 4h-4c.4-1.4 1.1-2.8 2-4zM4.3 14a8 8 0 0 1 0-4h3.5a16 16 0 0 0 0 4zm.8 2h3c.3 1.3.8 2.5 1.4 3.6A8 8 0 0 1 5.1 16zm3-8h-3a8 8 0 0 1 4.4-3.6C8.9 5.5 8.4 6.7 8.1 8zM12 20c-.9-1.2-1.6-2.6-2-4h4c-.4 1.4-1.1 2.8-2 4zm2.3-6H9.7a14 14 0 0 1 0-4h4.6a14 14 0 0 1 0 4zm.2 5.6c.6-1.1 1.1-2.3 1.4-3.6h3a8 8 0 0 1-4.4 3.6zm1.7-5.6a16 16 0 0 0 0-4h3.5a8 8 0 0 1 0 4z"/></svg>
        www.ncdb-build.com
      </li>
    </ul>
  </section>

</main>
</body>
</html>
```